Dog grooming business card
This is a business card for m dog grooming business like it say above.
In the priorities box below I will have the text that I want on the card.

Industry/Entity Type

Business

Colors

Designer to choose colors to be used in the design.

Requirements
Must have
• My logo and the insurance stamp must be on the card.

Text it must have :

Professional grooming services
Email: lunabrisk@mailvale.net
Text or call 1 705 318 6052
TWF certified/member
Pet first aid certified
Next appointment ___________________________________
Nice to have
• Greens to match my logo

```html
<!DOCTYPE html>
<html lang="en">
<head>
<meta charset="utf-8">
<title>Luna Brisk — Grooming Business Card</title>
<link rel="stylesheet" href="https://fonts.googleapis.com/css2?family=Noto+Serif:wght@400;700&display=swap">
<style>
  :root {
    --lime: #8dcb2c;
    --lime-soft: #9ad23a;
    --ink: #141014;
    --paper: #ffffff;
    --stage: #d9dcdf;
    --badge-blue: #2a6fd1;
    --badge-orange: #f08a1c;
  }
  * { box-sizing: border-box; margin: 0; padding: 0; }
  html, body { width: 1200px; height: 960px; overflow: hidden; }
  body {
    background: var(--stage);
    font-family: "Noto Serif", Georgia, serif;
    color: var(--ink);
    position: relative;
  }
  .card {
    position: absolute;
    left: 240px;
    width: 720px;
    height: 412px;
    background: var(--paper);
    overflow: hidden;
    box-shadow: 0 10px 28px rgba(0,0,0,.25);
  }
  .card--front { top: 48px; }
  .card--back { top: 500px; }

  /* front */
  .front__edge { position: absolute; left: 0; right: 0; height: 14px; background: var(--lime); }
  .front__band { position: absolute; left: 0; right: 0; height: 34px; background: var(--ink); }
  .front__edge--top { top: 0; }
  .front__band--top { top: 14px; }
  .front__edge--bottom { bottom: 0; }
  .front__band--bottom { bottom: 14px; }
  .front__logo {
    position: absolute; left: 50%; top: 50%;
    transform: translate(-50%, -50%);
  }

  .brand { display: flex; align-items: center; gap: 18px; }
  .brand__dot { border-radius: 50%; background: var(--lime); flex: none; }
  .brand__name { font-weight: 700; white-space: nowrap; }
  .front__logo .brand__dot { width: 96px; height: 96px; }
  .front__logo .brand__name { font-size: 54px; color: var(--ink); }

  /* back */
  .back__dark { position: absolute; left: 0; right: 0; top: 0; height: 160px; background: var(--ink); }
  .back__stripe { position: absolute; left: 0; right: 0; top: 160px; height: 14px; background: var(--lime); }
  .back__logo { position: absolute; left: 50%; top: 80px; transform: translate(-50%, -50%); }
  .back__logo .brand__dot { width: 78px; height: 78px; }
  .back__logo .brand__name { font-size: 40px; color: var(--lime); }

  .back__details {
    position: absolute; left: 0; right: 0; top: 190px;
    text-align: center;
    font-size: 21px; line-height: 31px;
  }
  .back__badge {
    position: absolute; right: 26px; top: 196px;
    width: 120px; height: 56px;
    border: 2px solid var(--badge-blue);
    border-radius: 10px;
    background: linear-gradient(90deg, #e8f0fb 0 60%, #fdf0e0 60% 100%);
  }
  .back__appointment {
    position: absolute; left: 28px; bottom: 26px; right: 160px;
    display: flex; align-items: flex-end; gap: 14px;
    font-size: 20px;
  }
  .back__line { flex: 1; border-bottom: 1.5px solid var(--ink); margin-bottom: 5px; }
</style>
</head>
<body>
  <section class="card card--front" aria-label="Card front">
    <div class="front__edge front__edge--top"></div>
    <div class="front__band front__band--top"></div>
    <div class="front__logo">
      <div class="brand">
        <span class="brand__dot"></span>
        <span class="brand__name">Luna Brisk</span>
      </div>
    </div>
    <div class="front__band front__band--bottom"></div>
    <div class="front__edge front__edge--bottom"></div>
  </section>

  <section class="card card--back" aria-label="Card back">
    <div class="back__dark"></div>
    <div class="back__stripe"></div>
    <div class="back__logo">
      <div class="brand">
        <span class="brand__dot"></span>
        <span class="brand__name">Luna Brisk</span>
      </div>
    </div>
    <div class="back__details">
      <p>Professional grooming services</p>
      <p>1 705 318 6052</p>
      <p>lunabrisk@mailvale.net</p>
      <p>TWF certified/member</p>
      <p>Pet first aid certified</p>
    </div>
    <div class="back__badge" role="img" aria-label="Insurance protection stamp"></div>
    <div class="back__appointment">
      <span>Next appointment</span>
      <span class="back__line"></span>
    </div>
  </section>
</body>
</html>
```